Luxury Business Card Design for High-End Window Treatments

Gilded Slatworks
Custom Plantation Shutters & Architectural Shading Systems

⸻

BACK

Daniel Trevick
Owner

Custom Interior & Exterior Window Treatments

919-555-0148
gildedslatworks.com

I have included a picture that I’m hoping we can use on the back, but I’m also wondering if you can get rid of the ladder? Should we get rid of shutters , shades and blinds underneath Gilded Slatworks?

Target Market(s)

High-end residential homeowners, custom home builders, architects, interior designers, and luxury renovation clients seeking premium plantation shutters and motorized architectural shading systems.

Industry/Entity Type

Custom Window treatments

Contact Information for Business Card

Front Gilded Slatworks Custom Plantation Shutters Motorized Architectural Shading Systems BACK Daniel Trevick Owner 919-555-0148 GildedSlatworks.com Custom Interior & Exterior Window Treatments By Appointment

Requirements
Nice to have
• Not 100% sure on nice to halves or the color but you can definitely check out my website to get a better understanding of what I’m trying to do

```html
<!DOCTYPE html>
<html lang="en">
<head>
<meta charset="utf-8">
<title>Gilded Slatworks – Business Card</title>
<link rel="stylesheet" href="https://fonts.googleapis.com/css2?family=Arvo:wght@700&family=Lora:wght@400;500&family=Marcellus&family=Montserrat:wght@400&display=swap">
<style>
  :root {
    --stage: #3a3a3c;
    --ink: #111111;
    --card-black: #1b1b1c;
    --gold: #d6bb72;
    --gold-deep: #a8823f;
    --gold-dark: #7a5630;
    --gold-light: #e0c885;
    --silver: #9a9a9c;
    --white: #f4f4f2;
  }
  * { margin: 0; padding: 0; box-sizing: border-box; }
  html, body {
    width: 1200px; height: 758px; overflow: hidden;
    background: var(--stage);
  }
  .canvas {
    width: 1200px; height: 758px;
    display: flex; align-items: center; justify-content: center; gap: 36px;
  }
  .card {
    position: relative;
    width: 560px; height: 340px;
    border-radius: 18px;
    overflow: hidden;
    box-shadow: 0 14px 30px rgba(0,0,0,.45);
  }

  /* Front */
  .card--front {
    background: linear-gradient(120deg, var(--gold-dark) 0%, #b8955a 25%, var(--gold-light) 48%, #c9a865 68%, var(--gold-dark) 100%);
    display: flex; flex-direction: column; align-items: center; justify-content: center;
    text-align: center;
  }
  .brand-name {
    font-family: "Lora", serif;
    font-weight: 400;
    color: var(--ink);
    font-size: 64px;
    line-height: 1.02;
  }
  .brand-name span { display: block; }
  .brand-name span + span { padding-left: 90px; }
  .front-services {
    margin-top: 26px;
    display: flex; gap: 34px;
    font-family: "Arvo", serif;
    font-weight: 700;
    font-size: 26px;
    color: var(--ink);
  }

  /* Back */
  .card--back { background: var(--card-black); }
  .back-photo {
    position: absolute; inset: 0;
    background:
      linear-gradient(rgba(20,20,22,.55), rgba(20,20,22,.65)),
      linear-gradient(100deg, #3b4147 0%, #46505a 35%, #2f3a2e 65%, #4a4338 100%);
  }
  .back-waves { position: absolute; inset: 0; }
  .back-brand {
    position: absolute; top: 26px; right: 34px;
    font-family: "Lora", serif;
    font-weight: 400;
    font-size: 38px;
    line-height: 1.05;
    color: var(--gold);
    text-align: right;
  }
  .contact {
    position: absolute; left: 30px; top: 186px;
  }
  .contact__name {
    font-family: "Marcellus", serif;
    font-size: 27px;
    letter-spacing: .5px;
    color: var(--gold);
  }
  .contact__role {
    font-family: "Montserrat", sans-serif;
    font-size: 14px;
    color: var(--white);
    margin-top: 1px;
  }
  .contact__tagline {
    font-family: "Lora", serif;
    font-weight: 500;
    font-size: 17px;
    line-height: 1.2;
    color: var(--gold);
    margin-top: 8px;
  }
  .contact__list { list-style: none; margin-top: 8px; }
  .contact__item {
    display: flex; align-items: center; gap: 8px;
    font-family: "Lora", serif;
    font-size: 15px;
    color: var(--white);
    line-height: 1.45;
  }
  .contact__icon { width: 16px; height: 16px; flex: none; }
</style>
</head>
<body>
<main class="canvas">

  <section class="card card--front" aria-label="Card front">
    <h1 class="brand-name"><span>Gilded</span><span>Slatworks</span></h1>
    <p class="front-services"><span>Shutters</span><span>Shades</span><span>Blinds</span></p>
  </section>

  <section class="card card--back" aria-label="Card back">
    <div class="back-photo" role="img" aria-label="Photo of a two-storey house with a covered front porch and shrubs"></div>
    <svg class="back-waves" viewBox="0 0 560 340" aria-hidden="true">
      <defs>
        <linearGradient id="gold-band" x1="0" y1="0" x2="1" y2="0">
          <stop offset="0" stop-color="#b8955a"/>
          <stop offset=".5" stop-color="#e0c885"/>
          <stop offset="1" stop-color="#a8823f"/>
        </linearGradient>
      </defs>
      <path d="M0,0 H560 V108 C500,150 420,165 320,172 C200,180 60,175 0,200 Z" fill="var(--silver)"/>
      <path d="M0,0 H560 V100 C500,142 420,156 320,163 C200,171 60,165 0,188 Z" fill="var(--card-black)"/>
      <path d="M0,0 H560 V88 C500,134 420,151 320,157 C200,163 60,155 0,178 Z" fill="url(#gold-band)"/>
      <path d="M0,0 H560 V70 C500,125 420,146 320,152 C200,158 60,145 0,168 Z" fill="var(--card-black)"/>
    </svg>

    <p class="back-brand">Gilded<br>Slatworks</p>

    <div class="contact">
      <h2 class="contact__name">DANIEL TREVICK</h2>
      <p class="contact__role">Owner</p>
      <p class="contact__tagline">Custom Interior &amp; Exterior<br>Window Treatments</p>
      <ul class="contact__list">
        <li class="contact__item">
          <svg class="contact__icon" viewBox="0 0 16 16" aria-hidden="true">
            <circle cx="8" cy="8" r="8" fill="var(--gold)"/>
            <path d="M5.2 4.2c.4-.3.8-.2 1 .2l.7 1.3c.2.3.1.7-.2.9l-.5.4c.4.9 1.1 1.7 2 2.1l.4-.5c.2-.3.6-.4.9-.2l1.3.7c.4.2.5.6.2 1l-.6.7c-.5.5-1.2.6-1.9.3-1.9-.9-3.3-2.3-4.1-4.2-.3-.7-.1-1.4.4-1.9z" fill="var(--card-black)"/>
          </svg>
          919-555-0148
        </li>
        <li class="contact__item">
          <svg class="contact__icon" viewBox="0 0 16 16" aria-hidden="true">
            <circle cx="8" cy="8" r="8" fill="var(--gold)"/>
            <circle cx="8" cy="8" r="4.2" fill="none" stroke="var(--card-black)" stroke-width="1.1"/>
            <path d="M3.8 8h8.4M8 3.8c-1.6 2.4-1.6 6 0 8.4M8 3.8c1.6 2.4 1.6 6 0 8.4" fill="none" stroke="var(--card-black)" stroke-width="1"/>
          </svg>
          gildedslatworks.com
        </li>
      </ul>
    </div>
  </section>

</main>
</body>
</html>
```